E learning Platform for privacy

Current website is as below and its more of a shell.
I need someone to take the text and content and design it properly.
https://study.vornaquill.com/

After that, design has to be implemented with elementor and wordpress
https://elementor.com/

```html
<!DOCTYPE html>
<html lang="en">
<head>
<meta charset="utf-8">
<title>Vornaquill Learning Centre – Log In</title>
<link rel="stylesheet" href="https://fonts.googleapis.com/css2?family=Poppins:wght@400;500;600;700&display=swap">
<style>
  :root {
    --page-bg: #fafafa;
    --ink: #0b0b0b;
    --muted: #6b6b6b;
    --field-bg: #f3f3f3;
    --brand-orange: #f46524;
    --accent-amber: #f7941d;
    --blush: #f8d9ce;
    --social-grey: #676767;
    --hill-dark: #454545;
    --hill-light: #5b5b5b;
  }
  * { box-sizing: border-box; margin: 0; padding: 0; }
  html, body { width: 1200px; height: 844px; overflow: hidden; }
  body {
    position: relative;
    background: var(--page-bg);
    font-family: "Poppins", sans-serif;
    color: var(--ink);
  }
  .hill { position: absolute; left: 0; top: 0; }
  .brand {
    position: absolute; left: 0; width: 1200px; top: 56px;
    text-align: center;
    font-size: 40px; font-weight: 600; letter-spacing: 2px;
    color: var(--muted);
    line-height: 60px;
  }
  .brand-dot {
    display: inline-block; width: 14px; height: 14px;
    background: var(--brand-orange); border-radius: 50%;
    margin-right: 12px; vertical-align: middle;
  }
  .hero-illustration {
    position: absolute; left: 85px; top: 336px; width: 284px; height: 411px;
    border-radius: 18px;
    background: linear-gradient(180deg, #f7b21a 0%, #e9c06a 18%, #c2c2c2 40%, #a6a6a6 100%);
  }
  .deco-ring {
    position: absolute; left: 994px; top: 282px; width: 27px; height: 27px;
    border: 2.5px solid var(--accent-amber); border-radius: 50%;
  }
  .deco-dot {
    position: absolute; left: 946px; top: 309px; width: 62px; height: 62px;
    background: var(--blush); border-radius: 50%;
  }
  .login-title {
    position: absolute; left: 0; width: 1200px; top: 250px;
    text-align: center;
    font-size: 36px; font-weight: 700; line-height: 41px;
  }
  .login-form { position: absolute; left: 405px; top: 361px; width: 388px; }
  .field {
    display: block; width: 388px; height: 49px;
    border: none; border-radius: 25px;
    background: var(--field-bg);
    padding-left: 32px;
    font-family: "Poppins", sans-serif; font-size: 16px; font-weight: 500;
    color: var(--muted);
    outline: none;
  }
  .field::placeholder { color: var(--muted); }
  .field + .field { margin-top: 11px; }
  .form-options {
    display: flex; justify-content: space-between; align-items: center;
    margin-top: 13px; padding-left: 7px; height: 24px;
  }
  .forgot-link {
    color: var(--brand-orange); font-size: 17px; font-weight: 500;
    text-decoration: none; border-bottom: 1px solid var(--brand-orange);
    line-height: 22px;
  }
  .remember { display: flex; align-items: center; font-size: 17px; font-weight: 500; color: var(--muted); }
  .remember-box {
    width: 17px; height: 17px; border: 2px solid var(--muted); border-radius: 3px;
    margin-right: 10px;
  }
  .sign-in {
    display: block; width: 388px; height: 49px; margin-top: 25px;
    border: none; border-radius: 25px;
    background: var(--brand-orange); color: #fff;
    font-family: "Poppins", sans-serif; font-size: 20px; font-weight: 500;
    letter-spacing: 0.5px;
  }
  .social-row {
    position: absolute; top: 614px; left: 514px;
    display: flex; gap: 9px;
  }
  .social-btn {
    width: 51px; height: 51px; border-radius: 50%;
    background: var(--social-grey); border: none;
  }
</style>
</head>
<body>
  <svg class="hill" width="1200" height="844" viewBox="0 0 1200 844" aria-hidden="true">
    <defs>
      <linearGradient id="hillShade" x1="0" y1="0" x2="1" y2="0">
        <stop offset="0" stop-color="#454545"/>
        <stop offset="1" stop-color="#5b5b5b"/>
      </linearGradient>
    </defs>
    <path d="M0 629 C40 632 70 640 110 636 C200 630 320 640 380 700 C430 750 480 800 515 844 L0 844 Z" fill="url(#hillShade)"/>
  </svg>

  <div class="brand"><span class="brand-dot"></span>Vornaquill</div>

  <div class="hero-illustration" role="img" aria-label="Illustration of a student with a laptop sitting on a stack of books, with a speech bubble"></div>

  <div class="deco-ring"></div>
  <div class="deco-dot"></div>

  <h1 class="login-title">Log In to Your Vornaquill<br>Learning Centre Account!</h1>

  <form class="login-form">
    <input class="field" type="email" placeholder="Email">
    <input class="field" type="password" placeholder="Password">
    <div class="form-options">
      <a class="forgot-link" href="https://study.vornaquill.com/">Forgot Password</a>
      <label class="remember"><span class="remember-box"></span>Remember me</label>
    </div>
    <button class="sign-in" type="button">SIGN IN</button>
  </form>

  <div class="social-row">
    <button class="social-btn" type="button" aria-label="Sign in with social account one"></button>
    <button class="social-btn" type="button" aria-label="Sign in with social account two"></button>
    <button class="social-btn" type="button" aria-label="Sign in with social account three"></button>
  </div>
</body>
</html>
```